Real Estate Card Design

I need a new business card! Below you will find my headshot, the company logo and a copy of my previous business card.

The card must contain the following information:

Dana Wexley
Sales Representative
FERNBROOK HOMES REALTY INC BROKERGE
204-517 Marsh Rd E, Oshawa ON L1H 4K7
Cell: 905-618-3074 Office:905-481-2696
www.danawexley.example dana@homesbywexley.example

I would like the card to portray security and class all the while being fresh and contemporary. I hold the key....

```html
<!DOCTYPE html>
<html lang="en">
<head>
<meta charset="utf-8">
<title>Dana Wexley – Business Card</title>
<link rel="stylesheet" href="https://fonts.googleapis.com/css2?family=Libre+Baskerville:wght@700&family=Open+Sans:wght@400;600&display=swap">
<style>
  :root {
    --page: #e9e9e7;
    --card: #0c100f;
    --brand-blue: #1f9fdb;
    --text-light: #f2f2f2;
    --emboss: #262d2b;
    --photo-dark: #141816;
    --photo-warm: #6b5a48;
  }
  * { margin: 0; padding: 0; box-sizing: border-box; }
  html, body {
    width: 1200px; height: 1021px; overflow: hidden;
    background: var(--page);
    font-family: "Open Sans", sans-serif;
  }
  .card {
    position: absolute; left: 200px;
    width: 800px; height: 457px;
    background: var(--card);
    overflow: hidden;
    box-shadow: 0 8px 24px rgba(0,0,0,.22);
  }
  .card-back { top: 30px; }
  .card-front { top: 521px; }

  /* back side */
  .back-brand {
    position: absolute; left: 0; top: 0; width: 100%; height: 100%;
    display: flex; align-items: center; justify-content: center; gap: 22px;
  }
  .back-square { width: 96px; height: 96px; background: var(--emboss); flex: none; }
  .back-name {
    color: var(--emboss); font-weight: 600;
    font-size: 22px; line-height: 1.35; letter-spacing: 2px; width: 330px;
  }

  /* front side */
  .brand {
    position: absolute; left: 50px; top: 48px;
    display: flex; align-items: center; gap: 14px;
  }
  .brand-square { width: 60px; height: 60px; background: var(--brand-blue); flex: none; }
  .brand-name {
    color: var(--text-light); font-weight: 600;
    font-size: 15px; line-height: 1.3; letter-spacing: 1.2px; width: 240px;
  }
  .agent-name {
    position: absolute; left: 50px; top: 148px;
    font-family: "Libre Baskerville", serif; font-weight: 700;
    font-size: 27px; color: var(--brand-blue); letter-spacing: 1px;
  }
  .agent-title {
    position: absolute; left: 50px; top: 188px;
    color: var(--text-light); font-size: 17px;
  }
  .address {
    position: absolute; left: 50px; top: 245px;
    color: var(--text-light); font-size: 17px; line-height: 1.5;
  }
  .address .website { color: var(--brand-blue); }
  .contact-list {
    position: absolute; left: 262px; top: 300px; list-style: none; z-index: 2;
    color: var(--text-light); font-size: 17px; line-height: 1.55;
  }
  .contact-list li { display: flex; align-items: center; gap: 8px; white-space: nowrap; }
  .contact-list svg { width: 16px; height: 16px; flex: none; }
  .headshot {
    position: absolute; right: 0; top: 70px; width: 250px; height: 387px;
    background: radial-gradient(ellipse at 55% 40%, var(--photo-warm) 0%, #2d2a26 45%, var(--photo-dark) 75%, var(--card) 100%);
  }
  .accent-band {
    position: absolute; left: 0; bottom: 0; width: 100%; height: 12px; z-index: 3;
    background: linear-gradient(90deg, var(--brand-blue) 0%, var(--brand-blue) 55%, rgba(31,159,219,.35) 100%);
  }
</style>
</head>
<body>
  <section class="card card-back">
    <div class="back-brand">
      <div class="back-square"></div>
      <div class="back-name">FERNBROOK HOMES REALTY INC BROKERGE</div>
    </div>
  </section>

  <article class="card card-front">
    <div class="brand">
      <div class="brand-square"></div>
      <div class="brand-name">FERNBROOK HOMES REALTY INC BROKERGE</div>
    </div>

    <h1 class="agent-name">DANA WEXLEY</h1>
    <p class="agent-title">Sales Representative</p>

    <p class="address">
      204-517 Marsh Rd E<br>
      Oshawa ON L1H 4K7<br>
      <span class="website">www.danawexley.example</span>
    </p>

    <ul class="contact-list">
      <li>
        <svg viewBox="0 0 20 20" aria-hidden="true"><rect x="5" y="1.5" width="10" height="17" rx="2" fill="none" stroke="var(--brand-blue)" stroke-width="1.8"/><circle cx="10" cy="15.5" r="1" fill="var(--brand-blue)"/></svg>
        905-618-3074
      </li>
      <li>
        <svg viewBox="0 0 20 20" aria-hidden="true"><path d="M4 2l4 1 1 4-2 2c1 2 3 4 5 5l2-2 4 1 1 4-2 2C9 19 1 11 2 4z" fill="var(--brand-blue)"/></svg>
        905-481-2696
      </li>
      <li>
        <svg viewBox="0 0 20 20" aria-hidden="true"><rect x="1.5" y="4" width="17" height="12" fill="none" stroke="var(--brand-blue)" stroke-width="1.8"/><path d="M1.5 4l8.5 7 8.5-7" fill="none" stroke="var(--brand-blue)" stroke-width="1.8"/></svg>
        dana@homesbywexley.example
      </li>
    </ul>

    <div class="headshot" role="img" aria-label="Portrait of the agent in a pinstripe suit holding up a house key"></div>

    <div class="accent-band"></div>
  </article>
</body>
</html>
```